Redesign of Velvet Groove Entertainment Card

I already have my logo and font design for my company name. I am looking to come up with a Unique way of having it on my business card. Just looking for a really hip, and professional business card while still using my logo design.

I have also enclosed the front and back of the card so you can see what I have now. Looking for something different.

Thank you!

Target Market(s)

Young to middle aged brides and grooms

Industry/Entity Type

Business

Requirements
Should not have
• Cheese

```html
<!DOCTYPE html>
<html lang="en">
<head>
<meta charset="utf-8">
<title>Velvet Groove Entertainment – Business Card</title>
<link href="https://fonts.googleapis.com/css2?family=Mulish:wght@400;600;700;800&display=swap" rel="stylesheet">
<style>
  :root {
    --page-bg: #e4e1dc;
    --card-bg: #f1f0ee;
    --card-edge: #cfccc8;
    --ink-dark: #3a3a3c;
    --ink-mid: #4a4a4d;
    --brand-blue: #1d2a78;
    --band-blue: #1c2674;
    --band-text: #c9cce0;
  }
  * { margin: 0; padding: 0; box-sizing: border-box; }
  html, body {
    width: 1200px; height: 970px; overflow: hidden;
    background: var(--page-bg);
    font-family: "Mulish", "Century Gothic", sans-serif;
  }
  .business-card {
    position: absolute; left: 100px; top: 207px;
    width: 1000px; height: 556px;
    background: var(--card-bg);
    border: 1px solid var(--card-edge);
    box-shadow: 0 10px 30px rgba(0,0,0,0.12);
  }
  .brand {
    position: absolute; left: 521px; top: 112px;
    display: flex; align-items: center; gap: 18px;
  }
  .brand-dot {
    width: 64px; height: 64px; border-radius: 50%;
    background: var(--brand-blue);
  }
  .brand-name {
    font-weight: 800; font-size: 44px; line-height: 1;
    color: var(--brand-blue); letter-spacing: 1px;
    text-transform: uppercase;
  }
  .person-name {
    position: absolute; left: 95px; top: 178px;
    font-weight: 700; font-size: 33px; color: var(--ink-dark);
  }
  .person-role {
    position: absolute; left: 95px; top: 238px;
    font-size: 23px; color: var(--ink-mid);
  }
  .contact-list {
    position: absolute; left: 95px; top: 322px;
    list-style: none;
  }
  .contact-item {
    display: flex; align-items: center; gap: 28px;
    height: 40px; font-size: 21px; color: var(--ink-mid);
  }
  .contact-icon { width: 28px; height: 28px; fill: var(--brand-blue); stroke: var(--brand-blue); }
  .social-band {
    position: absolute; left: 0; right: 0; top: 480px; height: 46px;
    background: var(--band-blue);
    display: flex; align-items: center; padding-left: 95px;
    font-size: 17px; font-weight: 600; color: var(--band-text);
    letter-spacing: 0.3px;
  }
</style>
</head>
<body>
  <div class="business-card">
    <div class="brand">
      <div class="brand-dot"></div>
      <div class="brand-name">Velvet Groove</div>
    </div>

    <h1 class="person-name">Marcus Hale</h1>
    <p class="person-role">Owner/DJ/Emcee</p>

    <ul class="contact-list">
      <li class="contact-item">
        <svg class="contact-icon" viewBox="0 0 28 28" aria-hidden="true">
          <path d="M3 10 Q14 2 25 10 L22 13 L19 11 L19 9 Q14 7 9 9 L9 11 L6 13 Z" stroke="none"/>
          <path d="M8 14 L20 14 L23 24 L5 24 Z" stroke="none"/>
          <circle cx="14" cy="19" r="2.5" fill="#f1f0ee" stroke="none"/>
        </svg>
        <span>555-204-SPIN (7746)</span>
      </li>
      <li class="contact-item">
        <svg class="contact-icon" viewBox="0 0 28 28" aria-hidden="true">
          <rect x="3" y="7" width="22" height="15" fill="none" stroke-width="2.4"/>
          <path d="M3 7 L14 16 L25 7 M3 22 L11 14 M25 22 L17 14" fill="none" stroke-width="2"/>
        </svg>
        <span>info@velvetgroove.com</span>
      </li>
      <li class="contact-item">
        <svg class="contact-icon" viewBox="0 0 28 28" aria-hidden="true">
          <circle cx="14" cy="14" r="11" fill="none" stroke-width="2.4"/>
          <path d="M3 14 H25 M14 3 V25 M14 3 Q6 14 14 25 M14 3 Q22 14 14 25" fill="none" stroke-width="1.8"/>
        </svg>
        <span>velvetgroove.com</span>
      </li>
    </ul>

    <div class="social-band">groovepage.com/velvetgrooveentertainment</div>
  </div>
</body>
</html>
```